Business cards to launch an education platform

Hi,
I am looking at having new business cards designed.
I am a startup, developing a web platform for schools and university, the education world. It's an online assessment system.
I would like a card that looks classy, and that is using the colors and the font of my logo.

I have attached:
1) my logo
2) A business card that I have designed quickly so you can have all the information required in the card, but I really don't like it.
3) The font that I am using (Lato Regular) to design my web platform
4) Some screenshots of my web platform so you can have a look at the style that I have.

Target Market(s)

Major market: Education system: Schools and university
Minor markets: Business in general

Industry/Entity Type

Business

Contact Information for Business Card

Clara Fenwick
Director

M: 0437 518 902
E: clara.fenwick@amberLoomSystems.com.au

Requirements
Must have
• The colors of my logo

```html
<!DOCTYPE html>
<html lang="en">
<head>
<meta charset="utf-8">
<title>Amber Loom Systems – Business Card</title>
<link rel="stylesheet" href="https://fonts.googleapis.com/css2?family=Lato:wght@300;400;700&display=swap">
<style>
  :root {
    --backdrop: #8c8c8c;
    --card-paper: #f1f1f2;
    --navy: #0f3d6e;
    --navy-deep: #03345f;
    --sky: #2a9fd6;
    --ink: #3d4450;
    --mist: #d8e1ea;
  }
  * { margin: 0; padding: 0; box-sizing: border-box; }
  html, body {
    width: 1105px;
    height: 1200px;
    overflow: hidden;
    background: var(--backdrop);
    font-family: "Lato", sans-serif;
  }
  .card {
    position: absolute;
    left: 182px;
    width: 746px;
    height: 425px;
  }
  .card--front { top: 119px; background: var(--card-paper); }
  .card--back { top: 637px; background: var(--navy-deep); }

  .brand-name {
    position: absolute;
    right: 47px;
    top: 122px;
    text-align: right;
    color: var(--navy);
    font-weight: 400;
    font-size: 31px;
    line-height: 1.15;
    letter-spacing: 2px;
  }

  .holder {
    position: absolute;
    left: 48px;
    top: 258px;
  }
  .holder-name {
    color: var(--navy);
    font-weight: 700;
    font-size: 27px;
    line-height: 1.1;
  }
  .holder-role {
    color: var(--sky);
    font-size: 20px;
    line-height: 1.3;
  }
  .divider {
    position: absolute;
    left: 48px;
    top: 325px;
    width: 651px;
    height: 1.5px;
    background: var(--sky);
  }
  .contact-list {
    position: absolute;
    left: 48px;
    top: 339px;
    list-style: none;
    color: var(--ink);
    font-size: 19px;
    font-weight: 300;
  }
  .contact-item {
    display: flex;
    align-items: center;
    height: 27px;
  }
  .contact-icon {
    width: 16px;
    height: 18px;
    margin-right: 12px;
    fill: var(--navy);
  }

  .back-brand {
    position: absolute;
    left: 0;
    right: 0;
    top: 178px;
    display: flex;
    justify-content: center;
    align-items: center;
    gap: 16px;
  }
  .back-brand-mark {
    width: 34px;
    height: 34px;
    background: var(--sky);
  }
  .back-brand-name {
    color: #ffffff;
    font-size: 32px;
    font-weight: 400;
    letter-spacing: 2px;
  }
  .website {
    position: absolute;
    left: 0;
    right: 0;
    top: 358px;
    text-align: center;
    color: var(--mist);
    font-size: 20px;
    letter-spacing: 0.5px;
  }
</style>
</head>
<body>
  <section class="card card--front">
    <div class="brand-name">AMBER LOOM<br>Systems</div>

    <div class="holder">
      <div class="holder-name">Clara Fenwick</div>
      <div class="holder-role">Director</div>
    </div>
    <div class="divider"></div>

    <ul class="contact-list">
      <li class="contact-item">
        <svg class="contact-icon" viewBox="0 0 16 18" aria-hidden="true">
          <path d="M4 0h8a2 2 0 0 1 2 2v14a2 2 0 0 1-2 2H4a2 2 0 0 1-2-2V2a2 2 0 0 1 2-2zm0 2.5v11h8v-11zm4 12.2a.9.9 0 1 0 0 1.8.9.9 0 0 0 0-1.8z"/>
        </svg>
        0437 518 902
      </li>
      <li class="contact-item">
        <svg class="contact-icon" viewBox="0 0 16 18" aria-hidden="true">
          <path d="M0 4h16v1.2L8 10 0 5.2zm0 2.6 8 4.8 8-4.8V14H0z"/>
        </svg>
        clara.fenwick@amberLoomSystems.com.au
      </li>
    </ul>
  </section>

  <section class="card card--back">
    <div class="back-brand">
      <span class="back-brand-mark"></span>
      <span class="back-brand-name">AMBER LOOM</span>
    </div>
    <div class="website">www.amberLoomSystems.com.au</div>
  </section>
</body>
</html>
```